Allied Health team of Physiotherapists & Occupational Therapists seek a business card design

We have our new logo, we now need our new business cards and stationary. Tidewell: Oedema & Family Clinic is seeking a generic card design to represent our whole team and individual cards for each therapist that incorporates our new logo to communicate our holistic approach that is calming, nuturing, supportive and welcoming.
Our Physiotherapists and Occupational Therapists assess, treat and provide education for people who are at risk of or who have lymphoedema. This is often as a result of treatment for cancer. We provide pre-operative and post-operative management and cancer rehabilitation in our Pilates studio. Our team also consists of Physiotherapists who have a strong interest in pelvic floor and continence management for both men and women.

Target Market(s)

Mainly women health conscious

Industry/Entity Type

Allied Health: Physiotherapy / Occupational Therapy

Contact Information for Business Card

Address: 14 Gallivant Ave Seabrook 3288 Phone: 84316570 fax: 8431 6578 Email: info@tidewellcareservices.com.au Website: tidewellcareservices.com.au Facebook address: facebook.com/TidewellOedemaAndFamilyCareClinic. Room to write appointments. Individual cards need to have name, office email and individual email and professional details

Requirements
Must have
• Logo as per uploaded documents

```html
<!DOCTYPE html>
<html lang="en">
<head>
<meta charset="utf-8">
<title>Tidewell Business Card</title>
<link rel="stylesheet" href="https://fonts.googleapis.com/css2?family=Cinzel:wght@600&family=Jost:wght@400&family=Figtree:wght@400;500;800&display=swap">
<style>
:root{
  --bg:#262626;
  --card:#ffffff;
  --peach:#f9b080;
  --peach-text:#f4a46f;
  --ink:#3a3a3a;
  --rule:#ececec;
  --dots:#8a8a8a;
}
*{box-sizing:border-box;margin:0;padding:0}
html,body{width:1200px;height:1200px;overflow:hidden;background:var(--bg)}
.canvas{position:relative;width:1200px;height:1200px}
.card{position:absolute;left:262px;width:686px;height:392px;background:var(--card);border-radius:24px;overflow:hidden}
.card-front{top:165px}
.card-back{top:653px}

/* front */
.brand{position:absolute;left:48px;top:110px;width:220px;height:170px;display:flex;flex-direction:column;align-items:center;justify-content:center;gap:10px;text-align:center}
.brand-dot{width:18px;height:18px;border-radius:50%;background:var(--peach)}
.brand-name{font-family:"Jost",sans-serif;font-weight:400;color:var(--peach-text);font-size:22px;line-height:1.25}
.divider{position:absolute;left:297px;top:62px;width:1px;height:280px;background:var(--rule)}
.details{position:absolute;left:325px;top:95px;font-family:"Jost",sans-serif;color:var(--ink)}
.person-name{font-family:"Cinzel",serif;font-weight:600;color:var(--peach-text);font-size:24px;letter-spacing:.3px;line-height:1}
.person-role{font-size:16px;margin-top:4px}
.contact{list-style:none;margin-top:14px}
.contact li{display:flex;align-items:flex-start;font-size:17.5px;line-height:21.5px}
.contact li.gap{margin-top:8px}
.contact svg{width:13px;height:13px;margin:4px 14px 0 0;flex:none;fill:var(--peach)}

/* back */
.watermark{position:absolute;left:215px;top:60px;width:260px;height:260px;display:flex;align-items:center;justify-content:center;font-family:"Jost",sans-serif;font-size:58px;color:var(--peach);opacity:.1}
.appt-title{position:absolute;left:56px;top:50px;font-family:"Figtree",sans-serif;font-weight:500;font-size:27px;color:var(--peach-text)}
.book-online{position:absolute;left:509px;top:44px;width:134px;height:27px;border-radius:9px;background:var(--peach);color:#fff;font-family:"Figtree",sans-serif;font-weight:800;font-style:italic;font-size:17px;display:flex;align-items:center;justify-content:center}
.appt-row{position:absolute;left:56px;width:580px;height:20px;display:flex;align-items:baseline;font-family:"Figtree",sans-serif;font-size:16px;color:var(--peach-text)}
.appt-row .label{flex:none}
.appt-row .line{border-bottom:2px dotted var(--dots);height:13px;margin:0 2px 0 0}
.appt-row .date-line{width:255px;margin-left:16px}
.appt-row .time-line{width:140px;margin-left:4px}
.appt-row .ampm{margin-left:8px}
.site-band{position:absolute;left:0;top:323px;width:100%;height:33px;background:var(--peach);color:#fff;font-family:"Figtree",sans-serif;font-size:16px;letter-spacing:4px;display:flex;align-items:center;justify-content:center}
</style>
</head>
<body>
<main class="canvas">
  <section class="card card-front">
    <div class="brand">
      <span class="brand-dot"></span>
      <span class="brand-name">Tidewell: Oedema<br>&amp; Family Clinic</span>
    </div>
    <div class="divider"></div>
    <div class="details">
      <h1 class="person-name">MAREN ASHBY</h1>
      <p class="person-role">Physiotherapist</p>
      <ul class="contact">
        <li><svg viewBox="0 0 12 12"><path d="M6 0a4.2 4.2 0 0 0-4.2 4.2C1.8 7.4 6 12 6 12s4.2-4.6 4.2-7.8A4.2 4.2 0 0 0 6 0zm0 6a1.8 1.8 0 1 1 0-3.6A1.8 1.8 0 0 1 6 6z"/></svg><span>14 Gallivant Ave<br>Seabrook 3288</span></li>
        <li class="gap"><svg viewBox="0 0 12 12"><path d="M2.4 0.5l2 2.3-1 1.5c.8 1.7 2.2 3.1 3.9 3.9l1.5-1 2.3 2-1.2 2C5.5 11 1 6.5.5 1.7z"/></svg><span>8431 6570</span></li>
        <li><svg viewBox="0 0 12 12"><path d="M3 0h6v3H3zM0 4h12v5h-2v3H2V9H0zm3 3v4h6V7z"/></svg><span>8431 6578</span></li>
        <li><svg viewBox="0 0 12 12"><path d="M0 2h12v1.2L6 7 0 3.2zm0 2.6l6 3.8 6-3.8V10H0z"/></svg><span>info@tidewellcareservices.com.au</span></li>
        <li><svg viewBox="0 0 12 12"><circle cx="6" cy="6" r="5.5"/><path d="M3 4c1 0 2 1 1.5 2S5 8 5.5 9.5M8 2.5c-.5 1 0 2 1 2.2" stroke="#fff" stroke-width="1" fill="none"/></svg><span>www.tidewellcareservices.com.au</span></li>
      </ul>
    </div>
  </section>

  <section class="card card-back">
    <div class="watermark" aria-hidden="true">Tidewell</div>
    <h2 class="appt-title">Next Appointment</h2>
    <div class="book-online">Book Online</div>
    <div class="appt-row" style="top:122px"><span class="label">Date :</span><span class="line date-line"></span><span class="label">Time :</span><span class="line time-line"></span><span class="ampm">AM/PM</span></div>
    <div class="appt-row" style="top:165px"><span class="label">Date :</span><span class="line date-line"></span><span class="label">Time :</span><span class="line time-line"></span><span class="ampm">AM/PM</span></div>
    <div class="appt-row" style="top:216px"><span class="label">Date :</span><span class="line date-line"></span><span class="label">Time :</span><span class="line time-line"></span><span class="ampm">AM/PM</span></div>
    <div class="appt-row" style="top:268px"><span class="label">Date :</span><span class="line date-line"></span><span class="label">Time :</span><span class="line time-line"></span><span class="ampm">AM/PM</span></div>
    <div class="site-band">TIDEWELLCARESERVICES.COM.AU</div>
  </section>
</main>
</body>
</html>
```